COMPANY NAME: Bright Harbor Ventures: Task Description: We are a new UK based business with global rea

Target Market

- Personal and professional development – 30-55 age group, corporate leaders, Eastern European and Asian markets
- On-assignment projects – Corporate market – Eastern European and Asian Markets
- Property investment - 35-65 age group, Europe, USA, Australia

What we need

We need logos and brand design for a suite of web platforms (website, twitter and Facebook profile). We would like to have a cohesive and consistent look across all of our online platforms. The design suite must therefore include social media logos, backgrounds and headers. Specifically we are looking for:

a. Facebook header/page design: likely to have a more youthful look

b. Website: Header, background and layout that is responsive to devices, iPhone primarily, then tablet, then PC (we have purchased a website building package from SiteKettle so if you are familiar with one of their themes, it would be great to have a design that fits with a theme you would recommend); Design should be able to accommodate a place to position video in the medium term but an image in the short term.

c. LinkedIn: header/logo; more corporate look

d. Twitter: background/logo

e. Powerpoint template: background and logo - simple and soft background not busy

f. Electronic Newsletter: logo, header and sidebar; simple and soft background not busy

h. Business card: sophisticated and simple

Colors

We have in mind a preference for colors from the purple family, maybe lavender, so as to appeal to all genders and age groups. Though we are happy to go with a recommendation if you think otherwise.

We would like a look that is professional, airy, bright, fresh, futuristic, insightful, friendly.

Ethos of the brand

- experiencing opportunity and being fulfilled in a changing world
- services are facilitated through insights
- support provided through our product, services and tailored approach to coaching/partnerships (which includes private client match-making)
- we are service providers and passionate about quality and modern leadership skills at all stages in life.

The company name is "Bright Harbor Ventures” - our main message is helping people move to the next level - through investments, personal and professional growth.

Some of our messaging

1. International Leadership in a new world.

2. New technology;

3. Informed;

4. Positively Influential

5. Making a difference;

6. Empowered;

7. Risk free investments;

8. Commercial opportunity;

9. Fulfilled living;

10. Carefree and Fun Living;

11. Progression;

12. Open-minded

13. Energy/dynamic

The Business:
The business is to move people very quickly out of situations that hold them back. the situations could be their own personal situations; their career; their jobs; their teams; their ideas; their finances; their financial opportunities. Remove their fears and give them the strategies to take action. The team are international and have 40 years experience between them in this area.

We do want to come across modern and dynamic, customer outcome focussed, building long-term relationships; international.
Updates

Project Deadline Extended
Reason: We have not found the right designs - we are not just looking for a website design but also images and logos. Most images we can see in the designs are stock images - very standard. We need an image which will be the face of the company, like the shop front window. This main image will be used on social media (top image) and also the home page of the website.

Target Market(s)

30-55 years
Eastern Europe; UK; Asia; Africa; Middle East
Personal, Professional, Corporate, and Financial Growth

Industry/Entity Type

Business Service

Contact Information for Business Card

Simple and stylish
the 3 areas of the business on the reverse -

International look - Offices in UK and San Francisco

Company name
web address www.brightharborventure.com
email director@brightharborventure.com
Facebook bright harbor venture
LinkedIn Bright Harbor Venture
Twitter Bright Harbor Venture
Telephone: +44 (0) 768 213 5597

Logo Text

Something that symbolises unlimited growth - probably not text - could use the word INSIGHT in some way

Number of Pages Required

1 page

Colors
e4daeb
f3f1f8
ffffff

Requirements
Must have
• social media symbols and address
• company name
• Melanie Thorpe
• Director
• Telephone +44 (0) 768 213 5597
• Website name www.brightharborventure.co.uk
• Reverse of Card:
• Discreet, Fast, Bright Harbor Consultancy
• Corporate, Professional, Personal & Property Investment
Nice to have
• not too angular; soft lines; not too cluttered (possibly social media on the reverse and just logo, name, number on the front?
Should not have
• too busy

```html
<!DOCTYPE html>
<html lang="en">
<head>
<meta charset="utf-8">
<title>Bright Harbor Ventures</title>
<link href="https://fonts.googleapis.com/css2?family=Roboto:wght@300;400;500&display=swap" rel="stylesheet">
<style>
:root{
  --purple:#b5529c;
  --purple-dark:#9d3f86;
  --ink:#222;
  --text:#555;
  --muted:#777;
  --bar:#2b2b2b;
  --light:#f3f3f3;
  --white:#fff;
  --fb:#3b5998;
  --li:#0e76a8;
  --tw:#1da1f2;
}
*{box-sizing:border-box;margin:0;padding:0}
html,body{width:738px;height:1200px;overflow:hidden;background:var(--white)}
body{font-family:'Roboto',sans-serif;color:var(--text);position:relative}
.abs{position:absolute}

.topbar{left:0;top:0;width:738px;height:22px;background:var(--bar);color:#eee;font-size:7px;display:flex;align-items:center;padding-left:55px;gap:8px}
.topbar .sep{width:1px;height:12px;background:#555}
.topbar .item{display:flex;align-items:center;gap:5px}
.social-mini{position:absolute;right:55px;top:2px;display:flex;gap:2px}
.social-mini span{width:18px;height:18px;display:block}

.header{left:0;top:22px;width:738px;height:48px;border-bottom:1px solid #eee}
.brand{left:54px;top:13px;font-size:15px;font-weight:500;color:var(--purple);letter-spacing:.1px}
.nav{right:67px;top:20px;display:flex;gap:17px;font-size:7.4px;color:#333}
.menu-icon{right:67px;top:20px}

.hero{left:0;top:70px;width:738px;height:326px;background:linear-gradient(90deg,#f2efeb 0%,#ebe6df 40%,#c9b7a4 60%,#4a5570 78%,#2d3650 100%)}
.hero-title{left:76px;top:123px;font-size:24px;font-weight:400;color:var(--ink)}
.hero-rule{left:77px;top:157px;width:20px;height:2px;background:var(--purple)}
.hero-text{left:77px;top:165px;width:265px;font-size:7.6px;line-height:12px;color:#333}
.btn{background:var(--purple);color:#fff;font-size:7px;font-weight:500;display:flex;align-items:center;justify-content:center;gap:5px}
.hero-btn{left:77px;top:196px;width:73px;height:23px}
.arrow-left{left:13px;top:146px;width:25px;height:24px;background:#555;opacity:.85}
.arrow-right{left:702px;top:146px;width:25px;height:24px;background:var(--purple)}
.arrow-left,.arrow-right{display:flex;align-items:center;justify-content:center}
.hero-down{left:352px;top:315px}

.section-title{width:738px;text-align:center;font-size:17px;font-weight:400;color:var(--ink)}
.welcome-title{left:0;top:436px}
.welcome-rule{left:360px;top:460px;width:18px;height:2px;background:var(--purple)}
.welcome-sub{left:0;top:469px;width:738px;text-align:center;font-size:7.4px;color:#555}
.video{left:71px;top:494px;width:289px;height:173px;background:linear-gradient(135deg,#6b5a48 0%,#b8a890 35%,#e8e4de 60%,#c9c2b6 100%)}
.play{left:199px;top:564px;width:32px;height:32px;border-radius:50%;background:var(--purple);display:flex;align-items:center;justify-content:center}
.welcome-copy{left:384px;top:498px;width:280px;font-size:7.3px;line-height:12.4px;color:#555}
.welcome-copy p{margin-bottom:7px}

.services-band{left:0;top:710px;width:738px;height:266px;background:var(--purple)}
.services-title{left:67px;top:735px;font-size:16px;color:#fff;font-weight:400}
.services-rule{left:67px;top:756px;width:18px;height:2px;background:#fff}
.services-photo{left:80px;top:757px;width:130px;height:188px;background:linear-gradient(180deg,#c98c7a 0%,#2c2f45 45%,#262a3c 85%,#a0794c 100%);border-radius:40px 40px 0 0}
.dots{left:240px;top:825px;display:flex;flex-direction:column;gap:3px}
.dots span{width:5px;height:5px;border:1px solid #fff;border-radius:50%;display:block;opacity:.8}
.card{top:742px;width:140px;height:185px;background:#fff;padding:16px 15px;box-shadow:0 2px 6px rgba(0,0,0,.2)}
.card h3{font-size:9.2px;font-weight:400;color:#222;margin-top:10px;letter-spacing:.2px}
.card .rule{width:14px;height:2px;background:var(--purple);margin:6px 0 7px}
.card ul{list-style:none;font-size:7.2px;line-height:10.6px;color:#333}
.card li{margin-bottom:2px}

.newsletter{left:54px;top:945px;width:630px;height:61px;background:var(--light)}
.newsletter h2{position:absolute;left:40px;top:13px;font-size:16px;font-weight:400;color:#222}
.newsletter p{position:absolute;left:40px;top:38px;font-size:7.4px;color:#666}
.news-input{left:264px;top:19px;width:250px;height:26px;background:#fff;font-size:6.4px;color:#888;padding:9px 11px}
.news-btn{left:514px;top:19px;width:84px;height:26px}

.foot-brand{left:54px;top:1055px;font-size:20px;font-weight:500;color:var(--purple)}
.foot-legal{left:54px;top:1094px;width:230px;font-size:7.4px;line-height:13px;color:#555}
.foot-col h4{font-size:11px;font-weight:400;color:#333;margin-bottom:8px}
.foot-nav{left:329px;top:1037px}
.foot-nav li{list-style:none;font-size:7.2px;color:#666;line-height:16.4px}
.foot-connect{left:471px;top:1037px}
.foot-social{display:flex;gap:7px;margin:5px 0 12px}
.foot-social span{width:30px;height:30px;display:block}
.contact-line{font-size:7.3px;color:#555;display:flex;align-items:center;gap:7px;line-height:13px}

.bottombar{left:0;top:1170px;width:738px;height:30px;background:var(--bar);color:#ddd;font-size:6.8px}
.bottombar .left{position:absolute;left:55px;top:12px}
.bottombar .right{position:absolute;right:55px;top:12px}
</style>
</head>
<body>

<div class="abs topbar">
  <div class="item">
    <svg width="8" height="8" viewBox="0 0 24 24"><path fill="#fff" d="M6.6 10.8a15 15 0 0 0 6.6 6.6l2.2-2.2c.3-.3.7-.4 1-.2 1.1.4 2.3.6 3.6.6.6 0 1 .4 1 1V20c0 .6-.4 1-1 1A17 17 0 0 1 3 4c0-.6.4-1 1-1h3.5c.6 0 1 .4 1 1 0 1.3.2 2.5.6 3.6.1.3 0 .7-.2 1z"/></svg>
    +44 (0) 768 213 5597
  </div>
  <div class="sep"></div>
  <div class="item">
    <svg width="8" height="6" viewBox="0 0 16 12"><rect width="16" height="12" fill="#fff"/><path d="M0 0l8 6 8-6" stroke="#2b2b2b" stroke-width="1.5" fill="none"/></svg>
    Director@brightharborventure.com
  </div>
  <div class="social-mini">
    <span style="background:var(--fb)"></span>
    <span style="background:var(--li)"></span>
    <span style="background:var(--tw)"></span>
  </div>
</div>

<div class="abs header">
  <div class="abs brand" style="top:13px">Bright Harbor Ventures</div>
  <nav class="abs nav" style="right:94px">
    <span>About You</span><span>About Us</span><span>Our Values</span><span>Testimonials</span><span>Social Media</span><span>News Alert</span>
  </nav>
  <svg class="abs menu-icon" width="12" height="9" viewBox="0 0 12 9"><path d="M0 1h12M0 4.5h12M0 8h12" stroke="#b5529c" stroke-width="1.2"/></svg>
</div>

<section class="abs hero" role="img" aria-label="Photograph of two smiling businessmen in suits reviewing work together in a bright office"></section>
<h1 class="abs hero-title">Bright Harbor Ventures</h1>
<div class="abs hero-rule"></div>
<p class="abs hero-text">our main message is helping people move to the next level - through investments, personal and professional growth.</p>
<div class="abs btn hero-btn">
  <svg width="8" height="6" viewBox="0 0 8 6"><path d="M0 3h7M4.5 .5L7 3 4.5 5.5" stroke="#fff" fill="none" stroke-width=".9"/></svg>
  READ MORE
</div>
<div class="abs arrow-left"><svg width="6" height="8" viewBox="0 0 6 8"><path d="M4.5 1L1.5 4l3 3" stroke="#fff" fill="none" stroke-width="1.3"/></svg></div>
<div class="abs arrow-right"><svg width="6" height="8" viewBox="0 0 6 8"><path d="M1.5 1l3 3-3 3" stroke="#fff" fill="none" stroke-width="1.3"/></svg></div>
<svg class="abs hero-down" width="34" height="30" viewBox="0 0 34 30"><path d="M0 0h34L17 30z" fill="#fff"/><path d="M17 7v8M14.5 12.5L17 15l2.5-2.5" stroke="#888" fill="none" stroke-width=".8"/></svg>

<h2 class="abs section-title welcome-title">Welcome To Bright Harbor Ventures</h2>
<div class="abs welcome-rule"></div>
<p class="abs welcome-sub">Hello and welcome to the company that works with you on your terms.</p>
<div class="abs video" role="img" aria-label="Video still of hands holding a sales report with bar charts on a desk beside a laptop and notebook"></div>
<div class="abs play"><svg width="10" height="11" viewBox="0 0 10 11"><path d="M1 0l9 5.5L1 11z" fill="#fff"/></svg></div>
<div class="abs welcome-copy">
  <p>If you seek an experienced and trusted partner to work with you on an assignment or simply want some strategies to move your personal or professional talents to the next level then you are in the right place.</p>
  <p>If you feel that the pace of change in business is so fast that to be an outstanding leader you should ensure you are brought up to speed regularly then you are in the right place.</p>
  <p>If you are hearing about the essential new leadership essentials and you are ready to hear how to adopt them into your life or business then you are at the right place.</p>
  <p>I am so convinced that you will be delighted with how fast you can make change happen.</p>
</div>

<section class="abs services-band"></section>
<h2 class="abs services-title">Services</h2>
<div class="abs services-rule"></div>
<div class="abs services-photo" role="img" aria-label="Photograph of a smiling young man in a dark sweater giving two thumbs up"></div>
<div class="abs dots"><span style="background:#fff"></span><span></span><span></span></div>

<div class="abs card" style="left:257px">
  <svg width="22" height="22" viewBox="0 0 22 22" fill="none" stroke="#444" stroke-width="1"><circle cx="7" cy="5" r="3.5"/><path d="M3 21v-8a4 4 0 0 1 8 0v8"/><circle cx="16" cy="15" r="4"/></svg>
  <h3>CONSULTANCY</h3><div class="rule"></div>
  <ul><li>Professional and Personal</li><li>Next Generation Leaders (16-30)</li><li>Consultation Options</li></ul>
</div>
<div class="abs card" style="left:401px">
  <svg width="22" height="22" viewBox="0 0 22 22" fill="none" stroke="#444" stroke-width="1"><path d="M3 19l2-6L16 2l4 4L9 17z"/><path d="M13.5 4.5l4 4M3 19l6-2"/></svg>
  <h3>ON ASSIGNMENT</h3><div class="rule"></div>
  <ul><li>Team Cohesion Strategy</li><li>Go To Market Strategy</li><li>Internationalisation Strategy</li></ul>
</div>
<div class="abs card" style="left:544px">
  <svg width="26" height="22" viewBox="0 0 26 22" fill="none" stroke="#444" stroke-width="1"><path d="M1 6l6-4 5 3 5-3 6 4-9 10z"/><path d="M9 12l3 3M12 10l3 3"/></svg>
  <h3>PRIVATE CLIENT</h3><div class="rule"></div>
  <ul><li>Promotion and cash-buyer matching</li><li>Investment: high return projects</li><li>Commercial: Hotels and Senior Housing</li><li>Prestige Residential: US, Australia, UK</li></ul>
</div>

<section class="abs newsletter">
  <h2>Newsletter</h2>
  <p>Enter your email &amp; Subscribe newsletter</p>
  <div class="abs news-input">Enter your email address</div>
  <div class="abs btn news-btn">
    <svg width="8" height="6" viewBox="0 0 8 6"><path d="M0 3h7M4.5 .5L7 3 4.5 5.5" stroke="#fff" fill="none" stroke-width=".9"/></svg>
    SUBSCRIBE
  </div>
</section>

<div class="abs foot-brand">Bright Harbor Ventures</div>
<p class="abs foot-legal">Bright Harbor Venture Limited, registered in England and Wales. Registeres number 10482915.</p>
<div class="abs foot-col foot-nav">
  <h4>Navigation</h4>
  <ul><li>About You</li><li>About Us</li><li>Our Values</li><li>Testimonials</li><li>Social Media</li><li>News Alert</li></ul>
</div>
<div class="abs foot-col foot-connect">
  <h4>Connect With Us</h4>
  <div class="foot-social">
    <span style="background:var(--fb)"></span>
    <span style="background:var(--li)"></span>
    <span style="background:var(--tw)"></span>
  </div>
  <div class="contact-line">
    <svg width="8" height="6" viewBox="0 0 16 12"><rect width="16" height="12" fill="#b5529c"/><path d="M0 0l8 6 8-6" stroke="#fff" stroke-width="1.5" fill="none"/></svg>
    Email: Director@brightharborventure.com
  </div>
  <div class="contact-line">
    <svg width="8" height="8" viewBox="0 0 24 24"><path fill="#b5529c" d="M6.6 10.8a15 15 0 0 0 6.6 6.6l2.2-2.2c.3-.3.7-.4 1-.2 1.1.4 2.3.6 3.6.6.6 0 1 .4 1 1V20c0 .6-.4 1-1 1A17 17 0 0 1 3 4c0-.6.4-1 1-1h3.5c.6 0 1 .4 1 1 0 1.3.2 2.5.6 3.6.1.3 0 .7-.2 1z"/></svg>
    Call: &nbsp;+44 (0) 768 213 5597
  </div>
</div>

<footer class="abs bottombar">
  <span class="left">Copyright 2016 | All Right Reserved</span>
  <span class="right">Terms &amp; Conditions | Privacy Policy</span>
</footer>

</body>
</html>
```